A5 Patient Information Booklet (Chiropractic Clinic) 4-8 pages

Here’s a polished, professional rewrite of your full brief and content, with clearer structure, corrected language, and a premium tone:

---

**Project Title:** Premium Patient Information Brochure (Chiropractic & Wellness Clinic)

---

### **Overview**

We are a health and wellness clinic seeking a premium, high-end patient information brochure to provide following a patient’s initial consultation and first treatment.

The purpose of this booklet is to:

* Reinforce trust and professionalism
* Help patients understand what to expect next
* Encourage adherence to care recommendations
* Position the clinic as calm, expert-led, and results-driven

---

### **Format**

* 4–8 page booklet (A5 or similar size)
* Print-ready and digital versions required

---

### **Target Audience**

Patients who have just completed their initial consultation and may have begun treatment. They may already be experiencing physical or mental changes, so the brochure should guide, reassure, and educate them on what comes next.

---

### **Tone & Style**

* Premium, calm, and reassuring
* Modern wellness aesthetic (not overly clinical)
* Clean layout with minimal clutter
* Soft, neutral colour palette (whites, creams, muted greens, soft blues)
* Elegant typography (e.g. Montserrat / Lato)
* High-end, trustworthy, and professional feel

---

### **Key Messages**

#### 1. Listen to Your Body

Patients may feel different after treatment. Reassure them that this is normal and part of the healing process.

#### 2. Post-Treatment Advice

* Stay well hydrated
* Rest if needed
* Avoid overexertion if the body requires recovery

#### 3. Healing is a Journey (Core Concept)

A strong visual metaphor of a **“road to recovery”** or **journey** should be central to the design.

This journey should clearly illustrate three phases:

* **Phase 1: Initial Care (Weeks 1–6)**
Focus: Reducing pain/discomfort, calming the body, and initiating response to treatment

* **Phase 2: Corrective Care (Weeks 6–12)**
Focus: Addressing underlying issues, improving function, and creating lasting change

* **Phase 3: Wellness / Maintenance (Ongoing)**
Focus: Maintaining progress, preventing relapse, and supporting long-term wellbeing

**Important:**

* Emphasise that this is not a quick fix
* Progress requires time and consistency
* Each patient follows an individualised care plan
* The journey should feel structured, positive, and achievable

#### 4. Personalised Care

Reinforce that every treatment plan is tailored specifically to the individual.

#### 5. Professional Reassurance

Patients should feel confident they are in expert hands and supported throughout their journey.

---

### **Design Direction**

* Use imagery that reflects calmness, progression, and wellness (e.g. pathways, nature, soft gradients)
* Avoid generic stock imagery
* **Only use original clinic images from website and social media**
* Prioritise white space and clarity
* Aim for a luxury spa/medical hybrid aesthetic

---

## **Content Structure (Page-by-Page)**

### **Front Cover**

* Clean, minimal, premium design
* Clinic branding

---

### **Page 1: Patient Case Summary**

**Title:** *Welcome to Fernwell Spine Studio*

Thank you for choosing Fernwell Spine Studio.

This booklet is designed to guide you through:

* What we found during your initial consultation
* Your personalised recommended treatment plan
* Your road to recovery
* Long-term wellness care
* Why we take the approach we do

---

### **Page 2: Your Care Journey**

**Stage 1: Your Initial Consultation**

Today we completed a comprehensive assessment of your health and function, including:

* Full case history and discussion of your symptoms and goals
* Orthopaedic and neurological testing
* Postural and movement assessment
* Initial treatment (where appropriate)

**What this tells us:**

* How your body is currently functioning
* Where areas of stress or dysfunction may be present
* The most appropriate and effective path forward for your care

---

### **Page 3: Your Suggested Treatment Plan**

Based on today’s findings, your recommended care plan is:

**______ treatments over ______ weeks**

This should be viewed alongside your *Road to Recovery* to help you understand what to expect.

We have also discussed:

* Expected timelines for improvement
* Available payment options

**After Treatment:**
It is common to feel different following treatment. This is a normal response as your body begins to adapt and respond.

We recommend:

* Staying well hydrated
* Allowing time for rest and recovery
* Avoiding overexertion if your body feels it needs it

---

### **Page 4: What to Expect Next**

Healing is not always linear—it is a process that occurs over time.

Your care will typically progress through the following stages:

* **Relief Care**
Focused on reducing discomfort and calming the body

* **Corrective Care**
Focused on addressing underlying issues and improving function
(This phase may include prescribed exercises)

* **Maintenance / Wellness Care**
Focused on sustaining progress, preventing recurrence, and supporting long-term health

---

### **Page 5: Understanding Chiropractic Care**

**What is Chiropractic?**
Chiropractic care focuses on the relationship between the spine, nervous system, and overall body function.

By improving spinal movement and alignment, chiropractic care helps support the nervous system, allowing the body to function and heal more effectively.

**About Fernwell Spine Studio**
At Fernwell Spine Studio, our approach is centred around personalised, patient-focused care. We aim to not only relieve symptoms but to address underlying causes and support long-term wellbeing.

---

### **Back Page**

* Clinic contact details
* Website
* Social media icons/handles

**Closing Message:**
“A healthier, stronger you—supported every step of the way.”

---

### **Deliverables**

* Print-ready PDF
* Editable source files

---

### **Additional Notes**

* The brochure should feel valuable and worth keeping
* Encourage long-term care in a subtle, non-pushy way
* Maintain clarity, readability, and strong visual hierarchy
* Balance professionalism with warmth and approachability

---

If you’d like, I can also turn this into **actual brochure copy (fully written, patient-facing text)** or help you refine it further for a designer.

Existing patients who want to feel better and look after themselves that is given after their initil consultation appointment

Chiropractic, wellness, health

• Montserrat or Lato

0094D4
00A9DD
6FCCEA
C7EBF8
E9F6FB
00AB8E
00BBA5
67D7C9
C6EFE9
E9F9F6
6B429C
8869AF
B7A5CE
E3DAEB
F3F0F8

• my own photos, look premium wellness, be clear and simple to understand for patients journey or what to expect next and over time
• USe my social media/website for ideas
• generic photos and images

```html
<!DOCTYPE html>
<html lang="en">
<head>
<meta charset="utf-8">
<title>Fernwell Spine Studio – Patient Booklet</title>
<link href="https://fonts.googleapis.com/css2?family=Montserrat:ital,wght@0,400;0,500;0,600;0,700;0,800;1,400&display=swap" rel="stylesheet">
<style>
:root{
  --blue:#0094D4; --blue-2:#00A9DD; --blue-3:#6FCCEA; --blue-4:#C7EBF8; --blue-5:#E9F6FB;
  --teal:#00AB8E; --teal-2:#00BBA5; --teal-3:#67D7C9; --teal-4:#C6EFE9;
  --purple:#6B429C; --purple-2:#8869AF; --purple-3:#B7A5CE; --purple-4:#E3DAEB;
  --pink:#E07BC4; --ink:#2b2b33; --muted:#5d5d68; --bg:#e4e4e6; --paper:#fbfbfc;
}
*{box-sizing:border-box;margin:0;padding:0}
html,body{width:1200px;height:2520px;overflow:hidden;background:var(--bg);font-family:'Montserrat',sans-serif;color:var(--ink)}
.spread{position:absolute;left:60px;width:1080px;height:760px;display:flex;box-shadow:0 14px 40px rgba(0,0,0,.18)}
.spread--covers{top:40px}.spread--aftercare{top:880px}.spread--plan{top:1720px}
.page{position:relative;width:540px;height:760px;background:var(--paper);overflow:hidden}
.page--left{box-shadow:inset -18px 0 24px -18px rgba(0,0,0,.18)}
.page--right{box-shadow:inset 18px 0 24px -18px rgba(0,0,0,.14)}
.photo{position:absolute;border-radius:28px}
.brand{font-weight:700;letter-spacing:.04em;text-transform:uppercase;color:var(--purple)}
.brand-mark{display:inline-block;border-radius:50%;border:3px solid var(--teal-2);vertical-align:middle}
.pill{position:absolute;border-radius:30px;font-weight:600;text-align:center;color:#fff}
.gradient-title{font-weight:800;text-transform:uppercase;line-height:1.02;background:linear-gradient(90deg,var(--blue-2),var(--purple-2) 55%,var(--pink));-webkit-background-clip:text;background-clip:text;color:transparent}
/* back cover */
.back-photo-a{left:60px;top:50px;width:190px;height:170px;background:linear-gradient(135deg,#8a7a70,#3b4a66)}
.back-photo-b{left:200px;top:90px;width:300px;height:210px;background:linear-gradient(135deg,#9a9a9a,#3a3a3a)}
.back-wave{position:absolute;left:0;top:300px}
.portrait{position:absolute;left:220px;top:440px;width:130px;height:130px;border-radius:50%;background:linear-gradient(135deg,#7a5a48,#d8b89a);border:4px solid #fff}
.portrait-caption{position:absolute;left:220px;top:582px;width:130px;text-align:center;color:#fff;font-size:13px;font-weight:500}
.back-brand{position:absolute;left:360px;top:418px;font-size:11px}
.back-address{position:absolute;left:40px;top:610px;width:460px;text-align:center;color:#fff;font-size:12px;line-height:1.5}
.back-address svg{display:block;margin:0 auto 4px}
.social{position:absolute;left:40px;top:560px;display:flex;gap:6px}
.social span{width:14px;height:14px;border-radius:50%;background:#fff}
.back-url{left:60px;top:680px;width:420px;height:42px;line-height:42px;background:#fff;color:var(--ink);font-size:17px}
/* front cover */
.cover-brand{position:absolute;left:0;right:0;top:70px;text-align:center}
.cover-brand .brand-mark{width:58px;height:58px}
.cover-brand .brand{display:block;margin-top:14px;font-size:22px}
.cover-title{position:absolute;left:40px;right:40px;top:180px;text-align:center;font-size:36px}
.cover-intro{position:absolute;left:70px;right:70px;top:330px;text-align:center;font-size:14px;line-height:1.55;color:var(--muted)}
.cover-photo{position:absolute;left:0;bottom:0;width:540px;height:330px}
.cover-url{left:110px;top:680px;width:320px;height:40px;line-height:40px;background:var(--teal-2);font-size:16px}
/* aftercare */
.after-title{position:absolute;left:40px;top:44px;font-size:40px;width:480px}
.after-intro{position:absolute;left:40px;top:190px;width:440px;font-size:13.5px;line-height:1.5;color:var(--muted)}
.after-band{position:absolute;left:0;top:250px}
.after-photo{position:absolute;left:140px;top:380px;width:260px;height:380px;border-radius:30px 30px 0 0;background:linear-gradient(160deg,#6d5142,#c9a88f 50%,#5a5a6e)}
.tip{position:absolute;border-radius:50%;background:#fff;border:12px solid var(--purple-3);display:flex;align-items:center;justify-content:center;text-align:center;font-size:17px;color:var(--ink);line-height:1.2;box-shadow:0 0 0 4px var(--pink) inset}
.tip--rest{left:250px;top:260px;width:130px;height:130px}
.tip--hydrate{left:30px;top:380px;width:140px;height:140px}
.tip--ease{left:340px;top:390px;width:180px;height:180px}
.recovery-chart{position:absolute;left:40px;top:50px;width:460px;height:330px;border:6px solid #333;border-radius:4px;box-shadow:0 10px 24px rgba(0,0,0,.15);background:linear-gradient(135deg,#fdf3e6 0%,#fbe3c4 35%,#e2f3dc 65%,#d6f1ec 100%)}
.phases{position:absolute;left:30px;right:30px;top:420px;height:300px}
.phase{position:absolute;width:160px;text-align:center}
.phase-tag{display:inline-block;background:var(--teal-3);color:#fff;font-size:10px;font-weight:600;padding:3px 12px;border-radius:10px}
.phase-icon{width:34px;height:34px;border-radius:50%;margin:8px auto;background:var(--blue-4);border:3px solid var(--blue-3)}
.phase h3{font-size:14px;font-weight:800;text-transform:uppercase;line-height:1.15}
.phase small{display:block;font-size:10px;font-weight:600;margin:3px 0;text-transform:uppercase;color:var(--muted)}
.phase p{font-size:11px;line-height:1.4;color:var(--muted)}
.phase--1{left:0;top:0}.phase--2{left:160px;top:70px}.phase--3{left:320px;top:140px}
/* plan */
.room-photo{position:absolute;inset:0;background:linear-gradient(180deg,#cfcbbf 0%,#b7b4a4 55%,#8a6e55 75%,#6f5642 100%)}
.plan-card{position:absolute;left:60px;top:60px;width:440px;height:560px;background:#fff;border-radius:40px;box-shadow:0 10px 30px rgba(0,0,0,.08)}
.plan-brand{position:absolute;left:0;right:0;top:50px;text-align:center}
.plan-brand .brand-mark{width:44px;height:44px}
.plan-brand .brand{display:block;margin-top:10px;font-size:17px}
.field{position:absolute;left:50px;right:50px;font-size:15px;color:var(--ink)}
.field::after{content:"";display:block;height:1px;background:#555;margin-top:34px}
.field--name{top:170px}.field--plan{top:260px}.field--treat{top:350px}
.field--weeks{top:440px;text-align:right}
.field--weeks::after{display:none}
</style>
</head>
<body>

<section class="spread spread--covers">
  <div class="page page--left back-cover">
    <div class="photo back-photo-a" role="img" aria-label="Chiropractor treating a patient in the clinic"></div>
    <div class="photo back-photo-b" role="img" aria-label="Black and white photo of a chiropractic adjustment"></div>
    <svg class="back-wave" width="540" height="460" viewBox="0 0 540 460" aria-hidden="true">
      <defs><linearGradient id="backGrad" x1="0" y1="1" x2="1" y2="0">
        <stop offset="0" stop-color="#00BBA5"/><stop offset=".5" stop-color="#6FCCEA"/><stop offset="1" stop-color="#B7A5CE"/></linearGradient></defs>
      <path d="M0 90 C120 10 300 10 540 80 L540 460 L0 460Z" fill="#B7A5CE" opacity=".55"/>
      <path d="M0 130 C150 60 320 70 540 150 L540 460 L0 460Z" fill="url(#backGrad)"/>
    </svg>
    <div class="portrait" role="img" aria-label="Portrait of the clinic chiropractor"></div>
    <div class="portrait-caption">Dr. Maren (DC)</div>
    <div class="back-brand"><span class="brand" style="color:#fff">Fernwell Spine Studio</span></div>
    <div class="social" aria-hidden="true"><span></span><span></span></div>
    <div class="back-address">
      <svg width="14" height="18" viewBox="0 0 14 18"><path d="M7 1a6 6 0 0 1 6 6c0 4-6 10-6 10S1 11 1 7a6 6 0 0 1 6-6z" fill="none" stroke="#fff" stroke-width="1.5"/><circle cx="7" cy="7" r="2" fill="#fff"/></svg>
      Fernwell Spine Studio Chiropractic &amp; Wellness<br>14 Orchard Row, Halbury HB3 7QT
    </div>
    <div class="pill back-url">www.fernwellspinestudio.com</div>
  </div>

  <div class="page page--right front-cover">
    <div class="cover-brand"><span class="brand-mark"></span><span class="brand">Fernwell Spine Studio</span></div>
    <h1 class="gradient-title cover-title">Align your body,<br>elevate your<br>wellbeing</h1>
    <p class="cover-intro">At Fernwell Spine Studio Chiropractic &amp; Wellness Halbury, we offer personalised chiropractic care for adults and families who want to feel their best — whether that's easing discomfort, improving movement, or supporting long-term wellbeing.</p>
    <svg class="cover-photo" viewBox="0 0 540 330" role="img" aria-label="Patient receiving a back treatment on a clinic couch">
      <defs>
        <linearGradient id="coverPhoto" x1="0" y1="0" x2="1" y2="1"><stop offset="0" stop-color="#d9c8bd"/><stop offset="1" stop-color="#9c7a62"/></linearGradient>
        <linearGradient id="coverWave" x1="0" y1="0" x2="1" y2="0"><stop offset="0" stop-color="#8869AF" stop-opacity=".85"/><stop offset="1" stop-color="#E07BC4" stop-opacity=".75"/></linearGradient>
      </defs>
      <path d="M0 60 C150 0 350 40 540 20 L540 330 L0 330Z" fill="url(#coverPhoto)"/>
      <path d="M0 60 C150 0 350 40 540 20 L540 150 C380 190 200 100 0 180Z" fill="url(#coverWave)"/>
    </svg>
    <div class="pill cover-url">www.fernwellspinestudio.com</div>
  </div>
</section>

<section class="spread spread--aftercare">
  <div class="page page--left">
    <h2 class="gradient-title after-title">What to<br>expect after<br>your treatment</h2>
    <p class="after-intro">Patients may feel different after treatment. Encourage awareness and reassurance that this is normal.</p>
    <svg class="after-band" width="540" height="510" viewBox="0 0 540 510" aria-hidden="true">
      <path d="M0 60 C140 0 300 40 540 10 L540 510 L0 510Z" fill="#00BBA5"/>
    </svg>
    <div class="after-photo" role="img" aria-label="Chiropractor adjusting a patient's neck"></div>
    <div class="tip tip--rest">Rest<br>if needed</div>
    <div class="tip tip--hydrate">Stay well<br>hydrated</div>
    <div class="tip tip--ease">Avoid<br>overexertion<br>if the body feels<br>like it needs<br>recovery</div>
  </div>

  <div class="page page--right">
    <div class="recovery-chart" role="img" aria-label="Road to recovery infographic showing progress through the care phases over time"></div>
    <div class="phases">
      <svg width="480" height="200" style="position:absolute;left:0;top:0" aria-hidden="true"><path d="M80 40 L240 110 L400 180" stroke="#6FCCEA" stroke-width="1.5" fill="none"/></svg>
      <div class="phase phase--1"><span class="phase-tag">PHASE 1</span><div class="phase-icon"></div><h3>Initial Care</h3><small>Weeks 1–6</small><p>Reducing pain/discomfort, calming the body, and helping you begin to respond to treatment.</p></div>
      <div class="phase phase--2"><span class="phase-tag">PHASE 2</span><div class="phase-icon"></div><h3>Corrective Care</h3><small>Weeks 6–12</small><p>Addressing underlying issues, improving function, and creating more stable, lasting changes.</p></div>
      <div class="phase phase--3"><span class="phase-tag">PHASE 3</span><div class="phase-icon"></div><h3>Wellness / Maintenance</h3><small>Ongoing</small><p>Maintaining progress, preventing relapse, and supporting long-term health and wellbeing.</p></div>
    </div>
  </div>
</section>

<section class="spread spread--plan">
  <div class="page page--left">
    <div class="plan-card">
      <div class="plan-brand"><span class="brand-mark"></span><span class="brand">Fernwell Spine Studio</span></div>
      <div class="field field--name">Patient Name</div>
      <div class="field field--plan">Your Suggested Care Plan</div>
      <div class="field field--treat">treatments over</div>
      <div class="field field--weeks">weeks</div>
    </div>
  </div>
  <div class="page page--right">
    <div class="room-photo" role="img" aria-label="Calm treatment room with a chiropractic couch and wooden floor"></div>
  </div>
</section>

</body>
</html>
```